Bourbon label design for bourbon brand. Looking to freshen our current label.

I need a Bourbon label design for our rebranded Bourbon bottle. Label should include picture of our horse and our logo on the bottle. Front Label is 3.5 inches wide and 6 inches tall, back label is 4 inches tall and 3 inches wide. Back label can be a simple plain logo like the one in the brief. I have included a design of our current bottle and label. We want to stay close to the current color schemes but want a fresh rebrand of the design. The label needs to be the correct size on a tall bottle like pictured.

Target Market(s)

Our Bourbon members, 30-50 year old males

Requirements
Must have
• Picture of our horse, our B logo , straight Bourbon whiskey on the front. Room to edit text on the back label.

```html
<!DOCTYPE html>
<html lang="en">
<head>
<meta charset="utf-8">
<title>Nightfall Straight Bourbon Whiskey – Front Label</title>
<link href="https://fonts.googleapis.com/css2?family=Rye&family=Crimson+Text:ital@0;1&display=swap" rel="stylesheet">
<style>
  :root {
    --label-black: #000000;
    --ink-white: #ffffff;
    --photo-light: #cfcbc6;
    --photo-mid: #8e8a86;
    --photo-dark: #3a3836;
  }
  html, body {
    margin: 0;
    padding: 0;
    width: 1116px;
    height: 1200px;
    overflow: hidden;
    background: var(--label-black);
  }
  .label {
    position: relative;
    width: 1116px;
    height: 1200px;
    background: var(--label-black);
    color: var(--ink-white);
    overflow: hidden;
  }
  .horse-photo {
    position: absolute;
    left: 385px;
    top: 68px;
    width: 322px;
    height: 426px;
    border-radius: 42% 42% 30% 30% / 22% 22% 12% 12%;
    background: radial-gradient(ellipse at 50% 40%, var(--photo-light) 0%, var(--photo-mid) 55%, var(--photo-dark) 85%, var(--label-black) 100%);
  }
  .est-tag {
    position: absolute;
    top: 271px;
    width: 100px;
    border-top: 2px solid var(--ink-white);
    border-bottom: 2px solid var(--ink-white);
    font-family: "Crimson Text", serif;
    font-size: 30px;
    line-height: 27px;
    padding: 2px 0 1px;
    text-align: center;
    letter-spacing: 1px;
  }
  .est-tag--left { left: 191px; }
  .est-tag--right { left: 785px; }
  .wordmark, .subtitle {
    position: absolute;
    left: 0;
    width: 1116px;
    overflow: visible;
  }
  .wordmark { top: 510px; height: 180px; }
  .subtitle { top: 712px; height: 60px; }
  .wordmark text, .subtitle text {
    font-family: "Rye", serif;
    fill: var(--ink-white);
  }
  .brand-mark {
    position: absolute;
    left: 0;
    top: 866px;
    width: 1116px;
    text-align: center;
    font-family: "Rye", serif;
    font-size: 52px;
    line-height: 60px;
  }
  .feature {
    position: absolute;
    top: 904px;
    font-family: "Crimson Text", serif;
    font-style: italic;
    font-size: 31px;
    line-height: 36px;
  }
  .feature--left { left: 180px; }
  .feature--right { left: 748px; top: 900px; }
  .fill-field {
    position: absolute;
    text-align: center;
    font-family: "Crimson Text", serif;
    font-size: 24px;
    line-height: 24px;
    letter-spacing: 1px;
  }
  .fill-field .fill-box {
    background: var(--ink-white);
    border-radius: 6px;
    margin-top: 2px;
  }
  .fill-field--barrel { left: 198px; top: 1076px; width: 162px; }
  .fill-field--barrel .fill-box { height: 35px; }
  .fill-field--aged { left: 484px; top: 1059px; width: 142px; }
  .fill-field--aged .fill-box { height: 58px; }
  .fill-field--abv { left: 751px; top: 1076px; width: 162px; }
  .fill-field--abv .fill-box { height: 35px; }
</style>
</head>
<body>
  <main class="label">
    <div class="horse-photo" role="img" aria-label="Black and white photograph of the brand's racehorse with jockey galloping toward the viewer"></div>

    <div class="est-tag est-tag--left">EST</div>
    <div class="est-tag est-tag--right">2016</div>

    <svg class="wordmark" viewBox="0 0 1116 180" aria-label="Nightfall">
      <text x="93" y="132" font-size="150" textLength="922" lengthAdjust="spacingAndGlyphs">NIGHTFALL</text>
    </svg>

    <svg class="subtitle" viewBox="0 0 1116 60" aria-label="Straight Bourbon Whiskey">
      <text x="208" y="44" font-size="44" textLength="706" lengthAdjust="spacingAndGlyphs">STRAIGHT BOURBON WHISKEY</text>
    </svg>

    <div class="brand-mark">Nightfall</div>

    <div class="feature feature--left">Single Barrel</div>
    <div class="feature feature--right">Cask Strength</div>

    <div class="fill-field fill-field--barrel">BARREL NO.<div class="fill-box"></div></div>
    <div class="fill-field fill-field--aged">AGED<div class="fill-box"></div></div>
    <div class="fill-field fill-field--abv">ALC/VOL<div class="fill-box"></div></div>
  </main>
</body>
</html>
```